Velmarotix - world unique technology for better life - please let them know who am i at first sight

We need a new business card for company which is a provider of unique crystal based technology suitable for all living being. For more information and final design you can use our brochure (our colours are black and blue from brochure).
We use Verdana font

Industry/Entity Type

Business

Contact Information for Business Card

regular dimension

Font styles to use
Other font styles liked:
• Verdana

Requirements
Must have
• Logo
• name
• function/position
• phone
• mobile
• e-mail
• adress
Nice to have
• inovative design (technology directed)

```html
<!DOCTYPE html>
<html lang="en">
<head>
<meta charset="utf-8">
<title>Velmarotix Business Card</title>
<link href="https://fonts.googleapis.com/css2?family=Open+Sans:wght@300;400;700&display=swap" rel="stylesheet">
<style>
  :root {
    --canvas: #e6e8ea;
    --card-black: #050505;
    --brand-blue: #1aa3e0;
    --text-light: #e8e8e8;
    --text-muted: #b9b9b9;
    --divider: #6a6a6a;
    --curl-light: #f2f2f2;
    --curl-dark: #9a9a9a;
  }
  * { margin: 0; padding: 0; box-sizing: border-box; }
  html, body { width: 1200px; height: 948px; overflow: hidden; }
  body {
    background: var(--canvas);
    font-family: "Open Sans", Verdana, sans-serif;
    position: relative;
  }
  .card {
    position: absolute;
    left: 250px;
    width: 700px;
    height: 400px;
    background: var(--card-black);
    overflow: hidden;
    box-shadow: 0 10px 30px rgba(0,0,0,0.25);
  }
  .card--front { top: 54px; }
  .card--back { top: 494px; }

  .wordmark {
    position: absolute;
    display: flex;
    align-items: center;
    gap: 18px;
    color: var(--brand-blue);
    font-weight: 300;
    letter-spacing: 3px;
    text-transform: uppercase;
  }
  .wordmark__dot {
    border-radius: 50%;
    background: var(--brand-blue);
    flex: none;
  }
  .card--front .wordmark { left: 150px; top: 58px; font-size: 44px; }
  .card--front .wordmark__dot { width: 64px; height: 64px; }
  .card--back .wordmark { left: 50%; top: 120px; transform: translateX(-50%); font-size: 50px; }
  .card--back .wordmark__dot { width: 76px; height: 76px; }

  .website {
    position: absolute;
    left: 0; right: 0;
    top: 236px;
    text-align: center;
    color: var(--text-light);
    font-size: 19px;
    font-weight: 700;
    letter-spacing: 3px;
  }

  .contact {
    position: absolute;
    left: 40px;
    top: 222px;
    display: flex;
    gap: 22px;
    color: var(--text-light);
    font-size: 15px;
  }
  .contact__list { list-style: none; }
  .contact__list li {
    display: flex;
    align-items: center;
    gap: 10px;
    line-height: 30px;
  }
  .contact__icon { width: 16px; height: 16px; flex: none; }
  .contact__divider { width: 1px; background: var(--divider); }
  .contact__address { font-style: normal; line-height: 30px; padding-top: 0; }

  .identity {
    position: absolute;
    right: 0;
    bottom: 0;
    width: 300px;
    height: 150px;
    background: var(--brand-blue);
  }
  .identity__curl { position: absolute; left: 0; top: 0; width: 300px; height: 150px; }
  .identity__text {
    position: absolute;
    right: 22px;
    top: 36px;
    text-align: right;
    color: #fff;
  }
  .identity__name { font-size: 22px; font-weight: 700; }
  .identity__role { font-size: 15px; font-weight: 400; margin-top: 4px; }
</style>
</head>
<body>

<section class="card card--front" aria-label="Business card front">
  <div class="wordmark"><span class="wordmark__dot"></span>Velmarotix</div>

  <div class="contact">
    <ul class="contact__list">
      <li>
        <svg class="contact__icon" viewBox="0 0 16 16"><path d="M3 1h3l1.5 4-2 1.3a8 8 0 0 0 4.2 4.2L11 8.5l4 1.5v3a2 2 0 0 1-2 2A13 13 0 0 1 1 3a2 2 0 0 1 2-2z" fill="#e8e8e8"/></svg>
        014-562-7380
      </li>
      <li>
        <svg class="contact__icon" viewBox="0 0 16 16"><rect x="4" y="1" width="8" height="14" rx="1.5" fill="none" stroke="#e8e8e8" stroke-width="1.6"/><circle cx="8" cy="12.3" r="0.9" fill="#e8e8e8"/></svg>
        014-562-7391
      </li>
      <li>
        <svg class="contact__icon" viewBox="0 0 16 16"><rect x="1" y="3" width="14" height="10" rx="1" fill="none" stroke="#e8e8e8" stroke-width="1.5"/><path d="M1.5 3.5 8 9l6.5-5.5" fill="none" stroke="#e8e8e8" stroke-width="1.5"/></svg>
        info@velmarotix.com
      </li>
      <li>
        <svg class="contact__icon" viewBox="0 0 16 16"><circle cx="8" cy="8" r="6.5" fill="none" stroke="#e8e8e8" stroke-width="1.4"/><ellipse cx="8" cy="8" rx="2.8" ry="6.5" fill="none" stroke="#e8e8e8" stroke-width="1.2"/><path d="M1.5 8h13" stroke="#e8e8e8" stroke-width="1.2"/></svg>
        www.velmarotix.cu
      </li>
    </ul>
    <span class="contact__divider"></span>
    <address class="contact__address">
      Street Name, City Name<br>
      Zipcode-0124
    </address>
  </div>

  <div class="identity">
    <svg class="identity__curl" viewBox="0 0 300 150" aria-hidden="true">
      <defs>
        <linearGradient id="curlShade" x1="0" y1="0" x2="1" y2="1">
          <stop offset="0" stop-color="#f2f2f2"/>
          <stop offset="0.55" stop-color="#cfcfcf"/>
          <stop offset="1" stop-color="#8a8a8a"/>
        </linearGradient>
      </defs>
      <path d="M0 0 L0 150 L110 150 Q55 120 35 70 Q20 35 0 0 Z" fill="#050505"/>
      <path d="M0 0 Q20 35 35 70 Q55 120 110 150 Q80 100 70 60 Q50 20 0 0 Z" fill="url(#curlShade)"/>
    </svg>
    <div class="identity__text">
      <div class="identity__name">Mira Kostanjevic</div>
      <div class="identity__role">Founder and CEO</div>
    </div>
  </div>
</section>

<section class="card card--back" aria-label="Business card back">
  <div class="wordmark"><span class="wordmark__dot"></span>Velmarotix</div>
  <div class="website">www.velmarotix.cu</div>
</section>

</body>
</html>
```